Letter and Envelope Design For Harborline Realty

Please design a letter and an envelope incorporating our logo (See Attached). We are also launched a business card contest. Since we want them to match, please feel free to submit a design for both the business card and also the letter design and envelope.

Requirements
Must have
• The envelope, the letter and the business cards must match somehow connecting the designs. We want them to have something that holds them together besides the logo.

```html
<!DOCTYPE html>
<html lang="en">
<head>
<meta charset="utf-8">
<title>Harborline Realty – Letterhead and Envelope</title>
<link rel="stylesheet" href="https://fonts.googleapis.com/css2?family=Montserrat:wght@600&family=Source+Sans+3:wght@400;700&display=swap">
<style>
  :root {
    --brand-blue: #0a1a8c;
    --heading-blue: #1a5fae;
    --ink: #2a2a2a;
    --muted: #555;
    --paper: #ffffff;
    --backdrop: #e7e7e7;
    --flap-mid: #6e6e76;
  }
  * { box-sizing: border-box; margin: 0; padding: 0; }
  html, body { width: 1200px; height: 825px; overflow: hidden; }
  body {
    background: var(--backdrop);
    position: relative;
    font-family: "Source Sans 3", sans-serif;
    color: var(--ink);
  }
  .sheet { position: absolute; background: var(--paper); }
  .letter { left: 81px; top: 71px; width: 482px; height: 682px; }
  .envelope-front { left: 602px; top: 75px; width: 518px; height: 226px; }
  .envelope-back { left: 602px; top: 330px; width: 518px; height: 226px; overflow: hidden; }

  .brand-stripe { position: absolute; background: var(--brand-blue); width: 20px; }
  .letter .brand-stripe { left: 30px; top: 0; bottom: 0; }
  .envelope-front .brand-stripe { left: 25px; top: -4px; bottom: 0; }

  .brand-dot {
    position: absolute; width: 42px; height: 42px; border-radius: 50%;
    background: var(--paper); border: 2px solid var(--brand-blue);
  }
  .letter .brand-dot { left: 19px; top: 20px; }
  .envelope-front .brand-dot { left: 14px; top: 15px; }

  .brand-name {
    position: absolute;
    font-family: "Montserrat", sans-serif; font-weight: 600;
    color: var(--brand-blue); font-size: 14px; letter-spacing: 1.6px; line-height: 16px;
  }
  .brand-name span { display: block; font-size: 9.5px; letter-spacing: 3.2px; padding-left: 30px; }
  .letter .brand-name { left: 66px; top: 32px; }
  .envelope-front .brand-name { left: 60px; top: 26px; }

  .web-vertical {
    position: absolute; color: var(--paper); font-size: 7px; white-space: nowrap;
    transform: rotate(-90deg); transform-origin: left top;
  }
  .letter .web-vertical { left: 36px; top: 660px; }
  .envelope-front .web-vertical { left: 31px; top: 213px; }

  .salutation {
    position: absolute; left: 68px; top: 96px;
    font-weight: 700; font-size: 11.5px; color: var(--heading-blue);
  }
  .letter-body { position: absolute; left: 68px; top: 122px; width: 382px; }
  .letter-body p {
    font-size: 10px; line-height: 12.6px; text-align: justify; margin-bottom: 12.6px;
  }
  .signature { position: absolute; left: 70px; top: 425px; width: 90px; height: 46px;
    background: linear-gradient(135deg, #f1f1f1, #dcdcdc); border-radius: 4px; }

  .contact-block { position: absolute; font-size: 7px; line-height: 9px; color: var(--muted); }
  .letter .contact-block { left: 367px; top: 617px; }
  .envelope-front .contact-block { left: 410px; top: 159px; }
  .contact-block .company { color: var(--brand-blue); font-weight: 700; font-size: 9px; line-height: 11px; }
  .contact-block .line { display: flex; align-items: center; gap: 4px; margin-top: 1px; }
  .contact-block .address { margin-bottom: 3px; }
  .contact-block svg { width: 7px; height: 7px; flex: none; }

  .flap { position: absolute; left: 0; top: 0; }
</style>
</head>
<body>

<section class="sheet letter" aria-label="Letterhead">
  <div class="brand-stripe"></div>
  <div class="brand-dot"></div>
  <div class="brand-name">HARBORLINE<span>REALTY</span></div>
  <div class="web-vertical">www.harborlinerealty.com</div>

  <h1 class="salutation">Dear Mr. Carter,</h1>
  <div class="letter-body">
    <p>Lorem Ipsum is simply dummy text of the printing and typesetting industry. Lorem Ipsum has been the industry's standard dummy text ever since the 1500s, when an unknown printer took a galley of type and scrambled it to make a type specimen book. It has survived not only five centuries, but also the leap into electronic typesetting, remaining essentially unchanged.</p>
    <p>The standard chunk of Lorem Ipsum used since the 1500s is reproduced below for those interested. Sections 1.10.32 and 1.10.33 from "de Finibus Bonorum et Malorum" by Aurelian are also reproduced in their exact original form, accompanied by English versions from the 1914 translation by L. Whitcombe</p>
    <p>Lorem Ipsum is simply dummy text of the printing and typesetting industry. Lorem Ipsum has been the industry's standard dummy text ever since the 1500s, when an unknown printer took a galley of type and scrambled it to make a type specimen book. It has survived not only five centuries, but also the leap into electronic typesetting, remaining essentially unchanged. It was popularised in the</p>
    <p>Lorem Ipsum is simply dummy text of the printing and typesetting industry. Lorem Ipsum has been the industry's standard dummy text ever since the 1500s, when an unknown printer took a galley of type and scrambled it to make a type specimen book. It has survived not only five centuries, but also the leap into electronic typesetting, remaining essentially unchanged. It was popularised in the</p>
  </div>
  <div class="signature" role="img" aria-label="Handwritten signature of the sender"></div>

  <address class="contact-block">
    <div class="company">Harborline Realty</div>
    <div class="address">Po. box 201, Street Name,<br>City Name, Zip Code - 00000</div>
    <div class="line"><svg viewBox="0 0 10 10"><circle cx="5" cy="5" r="5" fill="#0a1a8c"/><path d="M3 2.5 L4.3 2.5 L4.8 4 L4 4.6 Q4.8 6 5.6 6.2 L6.2 5.4 L7.5 6 L7.5 7.3 Q4 7.5 2.6 3.2Z" fill="#fff"/></svg>555-014-2290</div>
    <div class="line"><svg viewBox="0 0 10 10"><circle cx="5" cy="5" r="5" fill="#0a1a8c"/><rect x="2.5" y="3.2" width="5" height="3.6" fill="#fff"/><path d="M2.5 3.2 L5 5.2 L7.5 3.2" stroke="#0a1a8c" stroke-width=".6" fill="none"/></svg>info@harborlinerealty.com</div>
  </address>
</section>

<section class="sheet envelope-front" aria-label="Envelope front">
  <div class="brand-stripe"></div>
  <div class="brand-dot"></div>
  <div class="brand-name">HARBORLINE<span>REALTY</span></div>
  <div class="web-vertical">www.harborlinerealty.com</div>

  <address class="contact-block">
    <div class="company">Harborline Realty</div>
    <div class="address">Po. box 201, Street Name,<br>City Name, Zip Code - 00000</div>
    <div class="line"><svg viewBox="0 0 10 10"><circle cx="5" cy="5" r="5" fill="#0a1a8c"/><path d="M3 2.5 L4.3 2.5 L4.8 4 L4 4.6 Q4.8 6 5.6 6.2 L6.2 5.4 L7.5 6 L7.5 7.3 Q4 7.5 2.6 3.2Z" fill="#fff"/></svg>555-014-2290</div>
    <div class="line"><svg viewBox="0 0 10 10"><circle cx="5" cy="5" r="5" fill="#0a1a8c"/><rect x="2.5" y="3.2" width="5" height="3.6" fill="#fff"/><path d="M2.5 3.2 L5 5.2 L7.5 3.2" stroke="#0a1a8c" stroke-width=".6" fill="none"/></svg>info@harborlinerealty.com</div>
  </address>
</section>

<section class="sheet envelope-back" aria-label="Envelope back">
  <svg class="flap" width="518" height="226" viewBox="0 0 518 226">
    <defs>
      <linearGradient id="flapShade" x1="0" x2="1" y1="0" y2="0">
        <stop offset="0" stop-color="var(--brand-blue)" style="stop-color:#0a1a8c"/>
        <stop offset="0.5" stop-color="#6e6e76"/>
        <stop offset="1" stop-color="#0a1a8c"/>
      </linearGradient>
    </defs>
    <path d="M0 0 H518 C512 18 505 28 490 32 L300 64 Q259 74 218 64 L28 32 C13 28 6 18 0 0Z" fill="url(#flapShade)"/>
    <circle cx="259" cy="36" r="19" fill="none" stroke="#b9b9be" stroke-width="2"/>
  </svg>
</section>

</body>
</html>
```